Corvane Capital Business Cards

These are professional business cards that are for my family office.
Put fake emails and phone numbers as of now until I finalize those components. This family office controls my families investments, assets, and future. The cards should be professional.
..
.
.
.
I just uploaded another variation of a logo I would like to see as a business card to I am inbeteen which logo to use

Target Market(s)

business

Industry/Entity Type

business

Contact Information for Business Card

Professional, wealth related, finance related.

Requirements
Must have
• Logo

```html
<!DOCTYPE html>
<html lang="en">
<head>
<meta charset="utf-8">
<title>Corvane Capital Business Cards</title>
<link href="https://fonts.googleapis.com/css2?family=Poppins:wght@400;500;600&display=swap" rel="stylesheet">
<style>
  :root {
    --navy: #181d2a;
    --white: #ffffff;
    --grey: #a8a8a8;
    --rule: #9a9a9a;
    --backdrop: #e3e7e8;
  }
  * { margin: 0; padding: 0; box-sizing: border-box; }
  html, body {
    width: 1200px; height: 960px; overflow: hidden;
    background: var(--backdrop);
    font-family: "Poppins", sans-serif;
  }
  .card {
    position: absolute; left: 250px; width: 701px; height: 400px;
    border-radius: 22px; overflow: hidden;
  }
  .card-front { top: 61px; background: var(--navy); }
  .card-back { top: 501px; background: var(--white); }

  .front-mark {
    position: absolute; left: 261px; top: 82px;
    width: 180px; height: 180px; border-radius: 50%;
    border: 4px solid var(--white);
  }
  .front-name {
    position: absolute; left: 0; right: 0; top: 276px;
    text-align: center; color: var(--white);
    font-weight: 500; font-size: 34px; letter-spacing: 2px;
    text-transform: uppercase;
  }

  .back-mark {
    position: absolute; left: 103px; top: 125px;
    width: 116px; height: 116px; border-radius: 50%;
    border: 3px solid var(--navy);
  }
  .back-name {
    position: absolute; left: 0; width: 322px; top: 250px;
    text-align: center; color: var(--navy);
    font-weight: 500; font-size: 21px; letter-spacing: 1px;
    text-transform: uppercase;
  }
  .divider {
    position: absolute; left: 350px; top: 69px;
    width: 1px; height: 238px; background: var(--rule);
  }
  .person { position: absolute; left: 406px; top: 112px; color: var(--navy); }
  .person-name { font-size: 35px; line-height: 40px; font-weight: 400; }
  .person-name strong { font-weight: 600; }
  .person-title { font-size: 17px; font-weight: 500; margin-top: 2px; }

  .contacts { position: absolute; left: 405px; top: 198px; list-style: none; color: var(--navy); }
  .contacts li {
    display: flex; align-items: center; gap: 11px;
    font-size: 19px; line-height: 26px; height: 26px;
  }
  .contacts svg { width: 17px; height: 17px; flex: none; }

  .address-band {
    position: absolute; left: 0; top: 343px; width: 590px; height: 30px;
    background: var(--navy); color: var(--white);
    font-size: 17px; line-height: 30px; padding-left: 51px;
  }
  .accent-band {
    position: absolute; left: 645px; top: 343px; width: 56px; height: 30px;
    background: var(--grey);
  }
  .corner-mark {
    position: absolute; left: 586px; top: 326px;
    width: 66px; height: 66px; border-radius: 50%;
    background: var(--white); border: 2px solid var(--navy);
  }
</style>
</head>
<body>
  <section class="card card-front">
    <div class="front-mark"></div>
    <div class="front-name">Corvane Capital</div>
  </section>

  <section class="card card-back">
    <div class="back-mark"></div>
    <div class="back-name">Corvane Capital</div>
    <div class="divider"></div>

    <div class="person">
      <div class="person-name"><strong>Marta</strong> Velenska</div>
      <div class="person-title">Founder &amp; CEO</div>
    </div>

    <ul class="contacts">
      <li>
        <svg viewBox="0 0 24 24" aria-hidden="true"><path fill="#181d2a" d="M6.6 10.8a15.1 15.1 0 0 0 6.6 6.6l2.2-2.2a1 1 0 0 1 1-.25 11.4 11.4 0 0 0 3.6.57 1 1 0 0 1 1 1V20a1 1 0 0 1-1 1A17 17 0 0 1 3 4a1 1 0 0 1 1-1h3.5a1 1 0 0 1 1 1c0 1.25.2 2.45.57 3.57a1 1 0 0 1-.25 1z"/></svg>
        (555) 214-6037
      </li>
      <li>
        <svg viewBox="0 0 24 24" aria-hidden="true"><circle cx="12" cy="12" r="10" fill="none" stroke="#181d2a" stroke-width="2"/><path d="M2 12h20M12 2c3 3 3 17 0 20M12 2c-3 3-3 17 0 20" fill="none" stroke="#181d2a" stroke-width="1.6"/></svg>
        info@corvanecapital.com
      </li>
      <li>
        <svg viewBox="0 0 24 24" aria-hidden="true"><rect x="2" y="6" width="20" height="15" rx="1.5" fill="none" stroke="#181d2a" stroke-width="2"/><path d="M2 7l10 7 10-7" fill="none" stroke="#181d2a" stroke-width="2"/></svg>
        www.corvanecapital.com
      </li>
    </ul>

    <div class="address-band">4180 Linden Ave. Suite 300 Brookfield, TX 75510</div>
    <div class="accent-band"></div>
    <div class="corner-mark"></div>
  </section>
</body>
</html>
```